Laser Tattoo Removal Business Cards

We are looking for a professional business card design for a laser tattoo removal business. Ideally looking for a black business card design. The name of the business is Brightline Tattoo Removal. We place our cards at local tattoo shops so we ideally are looking for something trendy/edgy to draw both male and female clientele in.

Target Market(s)

Male/Female ages 18-60

Contact Information for Business Card

black background ideally.. hoping to stay within greys, whites and black

Font styles to use
Serif
Sans Serif

Colors
121212
a9a9a9
5c5c5c
f5f5f5
ffffff
7f7f7f
606060
848484
9d9d9d

Requirements
Must have
• Employee Info:
• Melissa Thornbury
• Chief Executive Offer
• m: 919.537.2846
• w: 919.362.4178
• f: 919.685.3907
• mthornbury@brightlinetattooremoval.example
• Address:
• 4615 Oakmere Pkwy, Suite 210
• Raleigh, NC 27654
• Website:
• www.brightlinetattooremoval.example
Nice to have
• Myabe business name on back or logo on back and employee info on the front

```html
<!DOCTYPE html>
<html lang="en">
<head>
<meta charset="utf-8">
<title>Brightline Tattoo Removal – Business Card</title>
<link href="https://fonts.googleapis.com/css2?family=Roboto:wght@400;500&display=swap" rel="stylesheet">
<style>
  :root {
    --backdrop: #d8d6d3;
    --card-ink: #121212;
    --band: #262626;
    --paper: #f5f5f5;
    --white: #ffffff;
    --text-dark: #3c3c3c;
    --text-mid: #5c5c5c;
  }
  * { margin: 0; padding: 0; box-sizing: border-box; }
  html, body {
    width: 1200px; height: 960px; overflow: hidden;
    background: var(--backdrop);
    font-family: "Roboto", Arial, sans-serif;
  }
  .canvas { position: relative; width: 1200px; height: 960px; }

  .card {
    position: absolute;
    width: 600px; height: 343px;
    box-shadow: 0 3px 8px rgba(0,0,0,.35);
  }

  /* Front */
  .card-front { left: 314px; top: 113px; background: var(--paper); }
  .front-band {
    position: absolute; left: 0; top: 30px;
    width: 100%; height: 162px;
    background: var(--band);
  }
  .person { position: absolute; left: 31px; top: 62px; color: var(--white); }
  .person-name { font-size: 19px; font-weight: 500; letter-spacing: .2px; text-transform: uppercase; line-height: 22px; }
  .person-title { font-size: 15px; font-weight: 400; line-height: 18px; }

  .brand {
    color: var(--white);
    font-weight: 500;
    text-transform: uppercase;
    text-align: center;
    display: flex; align-items: center; justify-content: center; gap: 12px;
  }
  .brand-mark { width: 12px; height: 12px; background: var(--white); flex: none; }
  .brand-name { line-height: 1.15; }
  .brand-name span { display: block; }

  .front-band .brand {
    position: absolute; right: 34px; top: 44px; width: 230px; height: 80px;
    font-size: 22px; letter-spacing: 2px;
  }
  .front-band .brand-name span + span { font-size: 15px; letter-spacing: 2.5px; }

  .contacts {
    position: absolute; left: 31px; top: 236px;
    list-style: none; color: var(--text-dark); font-size: 14px;
  }
  .contacts li { display: flex; align-items: center; height: 18.5px; }
  .contacts svg { width: 12px; height: 12px; margin-right: 10px; fill: var(--text-dark); flex: none; }
  .contacts .email { font-size: 13px; }

  .address {
    position: absolute; right: 32px; top: 236px;
    text-align: right; font-style: normal;
    color: var(--text-dark); font-size: 14px; line-height: 18.5px;
  }
  .address .web { font-size: 13px; }

  /* Back */
  .card-back { left: 311px; top: 472px; background: var(--card-ink); }
  .card-back .brand {
    position: absolute; left: 0; top: 100px; width: 100%; height: 130px;
    font-size: 40px; letter-spacing: 3px; gap: 18px;
  }
  .card-back .brand-mark { width: 16px; height: 16px; }
  .card-back .brand-name span + span { font-size: 20px; letter-spacing: 4px; margin-top: 8px; }
  .back-web {
    position: absolute; left: 0; bottom: 34px; width: 100%;
    text-align: center; color: var(--white);
    font-size: 13px; letter-spacing: 2.4px;
  }
</style>
</head>
<body>
<div class="canvas">

  <section class="card card-front">
    <div class="front-band">
      <div class="person">
        <div class="person-name">Melissa Thornbury</div>
        <div class="person-title">Chief Executive Offer</div>
      </div>
      <div class="brand">
        <span class="brand-mark"></span>
        <div class="brand-name"><span>Brightline</span><span>Tattoo Removal</span></div>
      </div>
    </div>

    <ul class="contacts">
      <li>
        <svg viewBox="0 0 24 24" aria-hidden="true"><path d="M6.6 10.8a15.1 15.1 0 0 0 6.6 6.6l2.2-2.2c.3-.3.7-.4 1-.2 1.1.4 2.3.6 3.6.6.6 0 1 .4 1 1V20c0 .6-.4 1-1 1A17 17 0 0 1 3 4c0-.6.4-1 1-1h3.5c.6 0 1 .4 1 1 0 1.3.2 2.5.6 3.6.1.3 0 .7-.2 1z"/></svg>
        919.362.4178
      </li>
      <li>
        <svg viewBox="0 0 24 24" aria-hidden="true"><path d="M7 1h10a2 2 0 0 1 2 2v18a2 2 0 0 1-2 2H7a2 2 0 0 1-2-2V3a2 2 0 0 1 2-2zm0 3v14h10V4zm5 15.5a1 1 0 1 0 0 2 1 1 0 0 0 0-2z"/></svg>
        919.537.2846
      </li>
      <li>
        <svg viewBox="0 0 24 24" aria-hidden="true"><path d="M7 2h10v5H7zM3 8h18a2 2 0 0 1 2 2v7h-4v5H5v-5H1v-7a2 2 0 0 1 2-2zm4 8v4h10v-4z"/></svg>
        919.685.3907
      </li>
      <li class="email">
        <svg viewBox="0 0 24 24" aria-hidden="true"><path d="M2 5h20v2l-10 6L2 7zm0 4.3 10 6 10-6V19H2z"/></svg>
        mthornbury@brightlinetattooremoval.example
      </li>
    </ul>

    <address class="address">
      4615 Oakmere Pkwy<br>
      Suite 210<br>
      Raleigh, NC 27654<br>
      <span class="web">www.brightlinetattooremoval.example</span>
    </address>
  </section>

  <section class="card card-back">
    <div class="brand">
      <span class="brand-mark"></span>
      <div class="brand-name"><span>Brightline</span><span>Tattoo Removal</span></div>
    </div>
    <div class="back-web">www.brightlinetattooremoval.example</div>
  </section>

</div>
</body>
</html>
```